Marlow Dermal Studio - Business Banner with Brand Elements

Design:
• We would like to get a creative design for a wide banner that will go outside our medical spa clinic location. We need a designer to make a simple yet colorful and high-quality design layout. We want this banner to be eye-catching and to communicate the services we offer at our business: Laser Hair Removal | Veluxin | Lip Filler.

Requirements:
• We would like the banner to include our companies information which is the following:

Logo
“Refresh Your Skin”
Laser Hair Removal | Veluxin | Lip Filler
(520) 867-2291
www.MarlowDermalStudio.com

Colors:
• Our business colors are orange, a hint of black and white, but mostly peach/orange tones. (Orange: #f78f20 , White: #ffffff)

Fonts:
• Josefins Sans Bold & Lato

Content and images can be located here:
https://files.quibbleshare.com/share/folders/7tKwP3zRa9_LmQxVb2nD5yHc04EeJuFs8?mode=viewing

The following will give you an idea of our brand presentation:
• Our website is: www.MarlowDermalStudio.com
• Our Pictavo; @marlowdermalstudio
• Our Lumora: www.lumoranet.com/marlowdermalstudio

Target Market(s)
• Women 25 - 45

Industry/Entity Type
• Beauty

```html
<!DOCTYPE html>
<html lang="en">
<head>
<meta charset="utf-8">
<title>Marlow Dermal Studio – Banner Concepts</title>
<link rel="stylesheet" href="https://fonts.googleapis.com/css2?family=Josefin+Sans:wght@600;700&family=Lato:wght@400;700&display=swap">
<style>
  :root {
    --board: #646464;
    --orange: #f78f20;
    --orange-deep: #f0751a;
    --orange-soft: #fbb24e;
    --peach-tint: #fdf1e8;
    --ink: #161616;
    --white: #ffffff;
    --sea: #7fd6d8;
    --sand: #efe6dc;
  }
  * { margin: 0; padding: 0; box-sizing: border-box; }
  html, body { width: 1200px; height: 927px; overflow: hidden; background: var(--board); }
  .board { position: relative; width: 1200px; height: 927px; }
  .banner { position: absolute; overflow: hidden; background: var(--white); }
  .banner svg.shapes { position: absolute; inset: 0; width: 100%; height: 100%; }
  .headline { font-family: "Josefin Sans", sans-serif; font-weight: 700; position: absolute; white-space: nowrap; line-height: 1; }
  .service-list { position: absolute; list-style: none; font-family: "Josefin Sans", sans-serif; font-weight: 700; color: var(--ink); }
  .service-list li { display: flex; align-items: center; gap: 5px; white-space: nowrap; }
  .dot { display: inline-block; width: 8px; height: 8px; border-radius: 50%; background: var(--orange); flex: none; }
  .contact { position: absolute; font-family: "Lato", sans-serif; color: var(--ink); white-space: nowrap; }
  .brand { position: absolute; display: flex; align-items: center; gap: 5px; font-family: "Josefin Sans", sans-serif; font-weight: 700; color: var(--ink); white-space: nowrap; line-height: 1; }
  .brand .mark { border-radius: 50%; background: var(--orange); flex: none; }
  .photo { position: absolute; }

  /* Concept 1 */
  .c1 { left: 57px; top: 51px; width: 525px; height: 245px; }
  .c1 .photo { inset: 0; background: linear-gradient(180deg, #8fdcdc 0%, #bfe8e6 40%, #dfe9e4 62%, var(--sand) 100%); }
  .c1 .headline { left: 298px; top: 63px; font-size: 22px; color: var(--white); }
  .c1 .service-list { left: 296px; top: 109px; font-size: 10px; }
  .c1 .service-list li { height: 20px; }
  .c1 .contact { left: 296px; top: 171px; font-size: 7px; font-weight: 700; }
  .c1 .brand { left: 296px; top: 203px; font-size: 13px; }
  .c1 .brand .mark { width: 16px; height: 16px; }

  /* Concept 2 */
  .c2 { left: 613px; top: 60px; width: 525px; height: 235px; }
  .c2 .headline { left: 25px; top: 40px; font-size: 23px; color: var(--ink); }
  .c2 .headline span { color: var(--orange); }
  .service-tiles { position: absolute; left: 14px; top: 92px; display: flex; gap: 17px; }
  .tile { width: 54px; display: flex; flex-direction: column; align-items: center; }
  .tile .photo { position: relative; width: 52px; height: 52px; border-radius: 50%; }
  .tile p { margin-top: 6px; font-family: "Josefin Sans", sans-serif; font-weight: 700; font-size: 7px; text-align: center; color: var(--ink); line-height: 1.2; }
  .c2 .contact { left: 26px; top: 185px; font-size: 7px; display: flex; gap: 14px; align-items: center; }
  .c2 .contact span { display: flex; align-items: center; gap: 4px; }

  /* Concept 3 */
  .c3 { left: 57px; top: 350px; width: 525px; height: 245px; }
  .c3 .photo { inset: 0; background: linear-gradient(180deg, #bfeef1 0%, #a7e2e5 45%, #d9ece9 66%, #f2ede6 100%); }
  .c3 .headline { left: 293px; font-size: 26px; }
  .c3 .h-top { top: 55px; color: var(--orange); letter-spacing: 0.5px; }
  .c3 .h-bottom { top: 83px; color: var(--ink); }
  .c3 .service-list { left: 296px; top: 114px; font-size: 10px; }
  .c3 .service-list li { height: 20px; }
  .c3 .contact { left: 298px; font-size: 8px; }
  .c3 .phone { top: 184px; }
  .c3 .web { top: 201px; }
  .c3 .brand { left: 14px; top: 14px; font-size: 11px; color: var(--white); }
  .c3 .brand .mark { width: 14px; height: 14px; background: var(--white); }

  /* Concept 4 */
  .c4 { left: 613px; top: 350px; width: 525px; height: 224px; }
  .c4 .photo { left: 280px; top: 40px; width: 270px; height: 270px; border-radius: 50%; background: linear-gradient(160deg, #6e7d8c 0%, #9aa6a8 45%, #e7b774 75%, #f0a033 100%); }
  .c4 .brand { left: 28px; top: 36px; font-size: 15px; }
  .c4 .brand .mark { width: 18px; height: 18px; }
  .c4 .headline { left: 29px; top: 73px; font-size: 27px; color: var(--ink); }
  .c4 .service-list { left: 28px; top: 108px; display: flex; gap: 16px; font-size: 10px; }
  .contact-pill { position: absolute; left: 27px; top: 137px; height: 20px; padding: 0 12px 0 9px; background: var(--orange); border-radius: 10px 10px 10px 0; display: flex; align-items: center; gap: 12px; font-family: "Lato", sans-serif; font-weight: 700; font-size: 7px; color: var(--white); white-space: nowrap; }
  .contact-pill span { display: flex; align-items: center; gap: 4px; }

  /* Concept 5 */
  .c5 { left: 57px; top: 642px; width: 525px; height: 200px; }
  .c5 .photo { inset: 0; background: linear-gradient(180deg, #c9e3ef 0%, #4cc3d4 22%, #8fdad8 48%, #e9e3d8 70%, #f3ebe1 100%); }
  .c5 .brand { left: 80px; top: 24px; font-size: 14px; }
  .c5 .brand .mark { width: 18px; height: 18px; }
  .offer-card { position: absolute; left: 34px; top: 62px; width: 197px; height: 108px; background: var(--orange); border: 3px solid var(--orange-soft); border-radius: 0 22px 0 22px; color: var(--white); text-align: center; }
  .offer-card .headline { position: static; margin-top: 17px; font-size: 19px; color: var(--white); }
  .offer-card .line { font-family: "Josefin Sans", sans-serif; font-weight: 700; font-size: 8px; margin-top: 6px; }
  .offer-card .info { font-family: "Lato", sans-serif; font-size: 7px; margin-top: 10px; line-height: 2.1; }
</style>
</head>
<body>
<main class="board">

  <section class="banner c1">
    <div class="photo" role="img" aria-label="Woman in a striped bikini on a sunny beach, sea in the background"></div>
    <svg class="shapes" viewBox="0 0 525 245" aria-hidden="true">
      <polygon points="325,0 525,0 525,245 214,245" fill="#ffffff" opacity="0.55"/>
      <polygon points="300,0 318,0 205,245 194,245" fill="var(--orange)"/>
      <polygon points="318,0 328,0 218,245 205,245" fill="#ffffff"/>
      <defs>
        <linearGradient id="band1" x1="0" x2="1"><stop offset="0" stop-color="var(--orange-deep)"/><stop offset="1" stop-color="var(--orange-soft)"/></linearGradient>
      </defs>
      <polygon points="270,49 525,49 525,98 247,98" fill="url(#band1)"/>
    </svg>
    <h2 class="headline">Refresh Your Skin</h2>
    <ul class="service-list">
      <li><i class="dot"></i>LASER HAIR REMOVAL</li>
      <li><i class="dot"></i>VELUXIN</li>
      <li><i class="dot"></i>LIP FILLER</li>
    </ul>
    <p class="contact">Phone: (520) 867-2291 &nbsp;|&nbsp; www.MarlowDermalStudio.com</p>
    <div class="brand"><i class="mark"></i>Marlow Dermal Studio</div>
  </section>

  <section class="banner c2">
    <svg class="shapes" viewBox="0 0 525 235" aria-hidden="true">
      <defs>
        <linearGradient id="trio" x1="0" x2="1"><stop offset="0" stop-color="#d8bea3"/><stop offset="0.5" stop-color="#b8835f"/><stop offset="1" stop-color="#d9b796"/></linearGradient>
      </defs>
      <path d="M 300 0 Q 235 70 240 235 L 236 235 Q 228 80 290 0 Z" fill="var(--orange)"/>
      <g role="img" aria-label="Three smiling women with glowing skin posed together">
        <path d="M 315 0 L 525 0 L 525 235 L 246 235 Q 240 80 315 0 Z" fill="url(#trio)"/>
      </g>
    </svg>
    <h2 class="headline"><span>Refresh</span> Your Skin</h2>
    <div class="service-tiles">
      <div class="tile"><div class="photo" role="img" aria-label="Laser hair removal treatment" style="background:linear-gradient(160deg,#c9b59c,#8fa3ad)"></div><p>LASER HAIR<br>REMOVAL</p></div>
      <div class="tile"><div class="photo" role="img" aria-label="Injection treatment on the forehead" style="background:linear-gradient(160deg,#cfd3d2,#8a8f8f)"></div><p>VELUXIN</p></div>
      <div class="tile"><div class="photo" role="img" aria-label="Lip filler treatment close-up" style="background:linear-gradient(160deg,#f5c2a0,#e07a5a)"></div><p>LIP FILLER</p></div>
    </div>
    <p class="contact">
      <span><i class="dot"></i>Phone: (520) 867-2291</span>
      <span><i class="dot"></i>www.MarlowDermalStudio.com</span>
    </p>
  </section>

  <section class="banner c3">
    <div class="photo" role="img" aria-label="Smiling woman in a straw hat on the beach"></div>
    <svg class="shapes" viewBox="0 0 525 245" aria-hidden="true">
      <path d="M 0 0 L 135 0 C 108 20 124 52 90 63 C 60 74 25 66 0 56 Z" fill="var(--orange)"/>
      <circle cx="0" cy="68" r="15" fill="var(--orange)"/>
      <path d="M 437 0 L 525 0 L 525 245 L 466 245 C 456 215 500 200 518 170 C 538 130 500 122 492 100 C 485 80 520 70 508 55 C 490 45 430 48 440 20 Z" fill="var(--orange)"/>
    </svg>
    <div class="brand"><i class="mark"></i>Marlow Dermal Studio</div>
    <h2 class="headline h-top">REFRESH</h2>
    <h2 class="headline h-bottom">YOUR SKIN</h2>
    <ul class="service-list">
      <li><i class="dot"></i>LASER HAIR REMOVAL</li>
      <li><i class="dot"></i>VELUXIN</li>
      <li><i class="dot"></i>LIP FILLER</li>
    </ul>
    <p class="contact phone">Phone: (520) 867-2291</p>
    <p class="contact web">www.MarlowDermalStudio.com</p>
  </section>

  <section class="banner c4">
    <svg class="shapes" viewBox="0 0 525 224" aria-hidden="true">
      <circle cx="70" cy="150" r="95" fill="var(--peach-tint)"/>
    </svg>
    <div class="photo" role="img" aria-label="Smiling woman in an orange off-shoulder top outdoors"></div>
    <div class="brand"><i class="mark"></i>Marlow Dermal Studio</div>
    <h2 class="headline">Refresh Your Skin</h2>
    <ul class="service-list">
      <li><i class="dot"></i>Laser Hair Removal</li>
      <li><i class="dot"></i>Veluxin</li>
      <li><i class="dot"></i>Lip Filler</li>
    </ul>
    <p class="contact-pill">
      <span><svg width="8" height="8" viewBox="0 0 10 10" aria-hidden="true"><circle cx="5" cy="5" r="5" fill="#fff"/><path d="M3 2.5 L4.3 2.5 L4.6 4 L3.9 4.5 Q4.6 5.8 5.6 6.2 L6.1 5.5 L7.5 5.8 L7.5 7.1 Q4 7.3 3 2.5 Z" fill="var(--orange)"/></svg>Phone: (520) 867-2291</span>
      <span><svg width="8" height="8" viewBox="0 0 10 10" aria-hidden="true"><circle cx="5" cy="5" r="4.2" fill="none" stroke="#fff"/><ellipse cx="5" cy="5" rx="1.8" ry="4.2" fill="none" stroke="#fff" stroke-width="0.8"/><line x1="0.8" y1="5" x2="9.2" y2="5" stroke="#fff" stroke-width="0.8"/></svg>www.MarlowDermalStudio.com</span>
    </p>
  </section>

  <section class="banner c5">
    <div class="photo" role="img" aria-label="Smiling woman lying on the sand at the water's edge"></div>
    <div class="brand"><i class="mark"></i>Marlow Dermal Studio</div>
    <div class="offer-card">
      <h2 class="headline">Refresh Your Skin</h2>
      <p class="line">Laser Hair Removal &nbsp;|&nbsp; Veluxin &nbsp;|&nbsp; Lip Filler</p>
      <p class="info">Phone: (520) 867-2291<br>www.MarlowDermalStudio.com</p>
    </div>
  </section>

</main>
</body>
</html>
```